New Business Card Design Project LORVANTI-Italy

we are LORVANTI-Italy
our company in the market for 3 years we are luxury cosmetic company and its about time for a facelift :)
i will like to have elegant luxurious and unique business card
that will give the person that get it a unique, luxurious and elegant impression
I'm VERY OPEN FOR NEW IDEAS , even duo i add a few files of things that i see on line and i like them

i add my logo as well
my website is LORVANTI.COM
(if you would like to see the main style that we have)

Target Market(s)

adult that have money :)

Industry/Entity Type

Business

Contact Information for Business Card

Name - Dario Lorvanti
Position - CEO and CO Founder
address - 4817 E Halvern
telephone - 555-384-1926
email - dario@lorvanti.com
fax - 555-384-1926
website - LORVANTI.COM

Colors
000000
959595
fbee3e
ffffff

Requirements
Must have
• big logo in GOLD color
• elegant look
• impressive
Nice to have
• not must but maybe classy pattern background
• not must but maybe emblem
• maybe clear plastic business card
Should not have
• colors
• images

```html
<!DOCTYPE html>
<html lang="en">
<head>
<meta charset="utf-8">
<title>LORVANTI Italy – Business Card</title>
<link rel="stylesheet" href="https://fonts.googleapis.com/css2?family=Cinzel:wght@500;600&family=Source+Sans+3:wght@400&display=swap">
<style>
  :root {
    --canvas: #ffffff;
    --ink: #000000;
    --paper: #ffffff;
    --gold: #c99f2c;
    --text: #111111;
    --edge: #e2e2e2;
  }
  * { margin: 0; padding: 0; box-sizing: border-box; }
  html, body { width: 1200px; height: 900px; overflow: hidden; background: var(--canvas); }
  .stage { position: relative; width: 1200px; height: 900px; }

  .card {
    position: absolute;
    top: 271px;
    width: 458px;
    height: 282px;
    border-radius: 14px;
    overflow: hidden;
    box-shadow: 2px 3px 5px rgba(0,0,0,0.35);
  }

  /* Front */
  .card-front { left: 137px; background: var(--paper); border: 1px solid var(--edge); }
  .front-band { position: absolute; left: 344px; top: 0; width: 114px; height: 100%; background: var(--ink); }
  .front-disc {
    position: absolute; left: 270px; top: 63px;
    width: 156px; height: 156px; border-radius: 50%;
    background: var(--paper);
  }
  .front-mark {
    position: absolute; left: 282px; top: 75px;
    width: 132px; height: 132px;
    display: flex; align-items: center; justify-content: center;
    font-family: "Cinzel", serif; font-weight: 600; font-size: 20px;
    color: var(--gold); letter-spacing: 1px;
  }

  .holder-name {
    position: absolute; left: 35px; top: 53px;
    font-family: "Cinzel", serif; font-weight: 600; font-size: 21px;
    color: var(--gold); letter-spacing: 0.5px;
  }
  .holder-role {
    position: absolute; left: 35px; top: 80px;
    font-family: "Source Sans 3", sans-serif; font-size: 14px; color: var(--text);
  }
  .contact-list { position: absolute; left: 35px; top: 116px; list-style: none; }
  .contact-list li {
    display: flex; align-items: center; height: 22.5px;
    font-family: "Source Sans 3", sans-serif; font-size: 14px; color: var(--text);
  }
  .contact-icon {
    width: 17px; height: 17px; border-radius: 50%; background: var(--ink);
    margin-right: 6px; display: flex; align-items: center; justify-content: center;
  }
  .contact-icon svg { width: 10px; height: 10px; fill: var(--gold); }
  .holder-address {
    position: absolute; left: 35px; top: 219px;
    font-family: "Source Sans 3", sans-serif; font-size: 14px; color: var(--text);
  }

  /* Back */
  .card-back { left: 626px; background: var(--ink); }
  .back-circle {
    position: absolute; left: 179px; top: 41px;
    width: 100px; height: 100px; border-radius: 50%;
    border: 3px solid var(--gold);
  }
  .back-name {
    position: absolute; left: 0; width: 100%; top: 160px; text-align: center;
    font-family: "Cinzel", serif; font-weight: 500; font-size: 40px;
    color: var(--gold); letter-spacing: 1px;
  }
</style>
</head>
<body>
<div class="stage">

  <section class="card card-front" aria-label="Business card front">
    <div class="front-band"></div>
    <div class="front-disc"></div>
    <div class="front-mark">LORVANTI</div>

    <h1 class="holder-name">DARIO LORVANTI</h1>
    <p class="holder-role">CEO and CO Founder</p>

    <ul class="contact-list">
      <li>
        <span class="contact-icon"><svg viewBox="0 0 10 10"><path d="M1 3.2C1 2 2 1.5 5 1.5S9 2 9 3.2V4H7V3.2H3V4H1Z M2 5h6l1 3.5H1Z"/></svg></span>
        555-384-1926
      </li>
      <li>
        <span class="contact-icon"><svg viewBox="0 0 10 10"><path d="M3 1h4v2H3Z M1.5 3.5h7v5h-7Z"/></svg></span>
        555-384-1926
      </li>
      <li>
        <span class="contact-icon"><svg viewBox="0 0 10 10"><path d="M1 2.5h8v5H1Z"/><path d="M1 2.5l4 3 4-3" fill="none" stroke="#000" stroke-width="0.8"/></svg></span>
        dario@lorvanti.com
      </li>
      <li>
        <span class="contact-icon"><svg viewBox="0 0 10 10"><circle cx="5" cy="5" r="4"/><path d="M1 5h8M5 1c-2 2.5-2 5.5 0 8M5 1c2 2.5 2 5.5 0 8" fill="none" stroke="#000" stroke-width="0.7"/></svg></span>
        WWW.LORVANTI.COM
      </li>
    </ul>

    <p class="holder-address">4817 E Halvern</p>
  </section>

  <section class="card card-back" aria-label="Business card back">
    <div class="back-circle"></div>
    <div class="back-name">LORVANTI</div>
  </section>

</div>
</body>
</html>
```